Investment Advisor E-Newsletter Banner Design

I need a banner designed for an email newsletter that will be sent monthly to clients and prospects. We want to see designs that are elegant and use our logo well. The banner should be 922x150px and should go well with the www.tlvbanda.com website. Should include Logo and email and phone number.

Target Market(s)

High net worth investors

Number of Pages Required

1 page

Requirements
Must have
• logo, place for email (info@tlvbanda.com) and phone number (415-297-6180), colors and design that work well with www.tlvbanda.com website

```html
<!DOCTYPE html>
<html lang="en">
<head>
<meta charset="utf-8">
<title>Talvera Banda Capital – Newsletter Banner</title>
<link rel="stylesheet" href="https://fonts.googleapis.com/css2?family=Cormorant+Garamond:ital,wght@1,500;1,600&display=swap">
<style>
  :root {
    --sky-deep: #4f8fdc;
    --sky-mid: #8cc2ee;
    --sky-pale: #e2f1fb;
    --ink-navy: #0c1a8e;
    --ink-grey: #5d6470;
    --face-white: #f7fbfe;
    --face-edge: #c9e2f5;
  }
  * { margin: 0; padding: 0; box-sizing: border-box; }
  html, body { width: 1200px; height: 195px; overflow: hidden; }
  body { font-family: "Cormorant Garamond", Georgia, serif; }

  .banner {
    position: relative;
    width: 1200px;
    height: 195px;
    overflow: hidden;
    background:
      radial-gradient(ellipse 420px 160px at 120px 40px, rgba(255,255,255,0.28), transparent 70%),
      linear-gradient(90deg, var(--sky-deep) 0%, var(--sky-mid) 45%, var(--sky-pale) 85%, var(--face-white) 100%);
  }

  .brand {
    position: absolute;
    left: 40px;
    top: 58px;
    display: flex;
    align-items: center;
    gap: 14px;
  }
  .brand-mark {
    width: 18px;
    height: 18px;
    background: var(--ink-navy);
  }
  .brand-name {
    font-style: italic;
    font-weight: 600;
    font-size: 40px;
    color: var(--ink-navy);
    white-space: nowrap;
  }

  .contact {
    position: absolute;
    left: 520px;
    top: 36px;
    font-style: italic;
    font-weight: 500;
    font-size: 35px;
    line-height: 48px;
  }
  .contact-label { color: var(--ink-grey); }
  .contact-value { color: var(--ink-navy); }

  .clock-art {
    position: absolute;
    left: 940px;
    top: -30px;
    width: 330px;
    height: 260px;
    border-radius: 50%;
    background: radial-gradient(circle at 45% 55%, var(--face-white) 0%, var(--face-white) 55%, var(--face-edge) 100%);
  }
</style>
</head>
<body>
  <header class="banner">
    <div class="brand">
      <span class="brand-mark"></span>
      <span class="brand-name">Talvera Banda Capital, Inc.</span>
    </div>

    <div class="contact">
      <p class="contact-line"><span class="contact-label">eMail:</span> <span class="contact-value">info@tlvbanda.com</span></p>
      <p class="contact-line"><span class="contact-label">Phone:</span><span class="contact-value">415-297-6180</span></p>
    </div>

    <div class="clock-art" role="img" aria-label="Illustration of a clock face with hands near twelve"></div>
  </header>
</body>
</html>
```